Inspiring Fundraising Foundation Website to Provide Academic Scholarships

Hello, we are launching a foundation to provide academic scholarships to high school students for college. We'd like this to be an informational website with contact information. There will be a total of approximately 5-7 pages in all.
The color scheme will be purple and white, with a girly feel. I 've attached the logo for reference!

Target Market(s)

high school students, college students

Industry/Entity Type

Education

Coding

Coded - Design and coding required

Number of Pages Required

5+ page

Font styles to use
Serif
Sans Serif
Script

Colors
6b449b
886aae
b7a5cd
e4daeb
ffffff
fdf9cf
fbf289

Requirements
Must have
• Purple, girly feel, to reflect the logo's style. Should be light-themed
Should not have
• No dark themes (aka heavy on black or dark colors)

```html
<!DOCTYPE html>
<html lang="en">
<head>
<meta charset="utf-8">
<title>Amara Lindell Foundation</title>
<link href="https://fonts.googleapis.com/css2?family=Raleway:wght@400;500;600;700&family=Open+Sans:wght@400;600&family=Kaushan+Script&display=swap" rel="stylesheet">
<style>
:root{
  --purple:#6b449b;
  --purple-mid:#886aae;
  --purple-soft:#b7a5cd;
  --purple-pale:#e4daeb;
  --white:#ffffff;
  --cream:#fdf9cf;
  --yellow:#fbf289;
  --ink:#333333;
  --muted:#555555;
  --footer-bg:#f6f5f7;
}
*{margin:0;padding:0;box-sizing:border-box}
html,body{width:1200px;height:3191px;overflow:hidden}
body{position:relative;background:var(--white);font-family:"Open Sans",Arial,sans-serif;color:var(--ink)}
.abs{position:absolute}
.script{font-family:"Kaushan Script",cursive;font-weight:400}
.raleway{font-family:"Raleway",Arial,sans-serif}

/* header */
.topbar{top:0;left:0;width:1200px;height:79px;background:var(--white)}
.phone{top:24px;right:162px;font-family:"Raleway",sans-serif;font-weight:700;font-size:21px;color:var(--purple);display:flex;align-items:center;gap:10px;letter-spacing:.5px}
.nav{top:79px;left:0;width:1200px;height:53px;background:var(--purple)}
.nav-list{position:absolute;left:345px;top:0;height:53px;display:flex;list-style:none}
.nav-list li{font-family:"Raleway",sans-serif;font-weight:700;font-size:13px;color:var(--white);height:53px;line-height:53px;padding:0 22px;text-transform:uppercase}
.nav-list li.active{background:var(--yellow);color:var(--purple);width:134px;text-align:center;margin-left:auto}
.brand{top:0;left:166px;width:145px;height:166px;border-radius:0 0 73px 73px;background:var(--white);z-index:5;display:flex;align-items:center;justify-content:center;text-align:center;font-family:"Raleway",sans-serif;font-weight:700;font-size:21px;line-height:1.15;color:var(--purple)}

/* hero */
.hero{top:132px;left:0;width:1200px;height:511px;background:linear-gradient(100deg,#c9b7a5 0%,#e2d6c8 30%,#d8d4cf 55%,#cbb48a 85%,#b99a66 100%)}
.hero-title{top:142px;right:158px;width:520px;text-align:right;font-family:"Raleway",sans-serif;font-weight:600;font-size:36px;line-height:1.33;color:var(--white)}
.btn-apply{top:306px;left:890px;width:148px;height:49px;background:var(--yellow);color:var(--purple);font-family:"Raleway",sans-serif;font-weight:700;font-size:15px;text-transform:uppercase;display:flex;align-items:center;justify-content:center}
.arrow{top:235px}

/* audience columns */
.audience{top:643px;left:0;width:1200px;height:308px;display:flex}
.aud-col{width:400px;height:308px;padding:74px 0 0 54px;color:var(--white)}
.aud-col:nth-child(1){background:var(--purple)}
.aud-col:nth-child(2){background:var(--purple-mid)}
.aud-col:nth-child(3){background:var(--yellow);color:var(--purple)}
.aud-col h3{font-family:"Raleway",sans-serif;font-weight:500;font-size:25px;margin-bottom:18px}
.aud-col h3 .script{font-size:25px;margin-right:4px}
.aud-col p{font-size:11px;line-height:19px;width:280px;margin-bottom:18px}
.aud-col:nth-child(3) p{color:var(--ink)}
.btn-line{display:inline-flex;align-items:center;justify-content:center;width:110px;height:37px;border:1px solid currentColor;font-family:"Raleway",sans-serif;font-weight:700;font-size:11px;text-transform:uppercase}
.aud-col:nth-child(3) .btn-line{color:var(--ink)}

/* section titles */
.section-title{left:162px;width:876px;text-align:center;font-family:"Raleway",sans-serif;font-size:28px;color:var(--ink);border-top:1px solid #e3e3e3}
.section-title .script{font-size:28px;margin-right:4px}

/* cards */
.card{top:1124px;width:272px}
.card .photo{width:272px;height:157px}
.card h4{margin-top:30px;font-family:"Raleway",sans-serif;font-weight:700;font-size:17px;color:var(--purple)}
.card p{margin-top:12px;font-size:11px;line-height:18px;color:var(--muted)}
.card .btn-line{margin-top:20px;color:var(--purple);width:104px;height:39px}

/* about band */
.about{top:1553px;left:0;width:1200px;height:469px;background:linear-gradient(90deg,#e8efe0 0%,#f4f6ef 60%,#ffffff 100%)}
.about-photo{top:1553px;left:0;width:617px;height:469px;background:linear-gradient(120deg,#d6dfc2 0%,#c9d2ae 40%,#b8463c 70%,#a33a33 100%)}
.about-title{top:1688px;left:655px;font-family:"Raleway",sans-serif;font-weight:700;font-size:26px;color:var(--purple)}
.about-title .script{font-weight:400}
.about-text{top:1742px;left:655px;width:385px;font-size:11px;line-height:20px;color:var(--ink)}

/* testimonials */
.testimonials{top:2022px;left:0;width:1200px;height:404px;background:var(--purple)}
.test-title{top:2078px;left:162px;font-size:24px;color:var(--white)}
.quote{top:2125px;left:162px;width:880px;font-family:"Raleway",sans-serif;font-size:23px;line-height:38px;color:var(--white)}
.quote-mark{font-family:Georgia,serif;font-weight:700;font-size:40px;vertical-align:-8px;margin-right:6px}
.quote-by{top:2316px;left:162px;font-family:"Raleway",sans-serif;font-weight:700;font-size:13px;color:var(--white);text-transform:uppercase}
.dots{top:2362px;left:162px;display:flex;gap:5px}
.dots span{width:11px;height:11px;border-radius:50%;background:var(--white)}
.dots span:first-child{background:transparent;border:1px solid var(--white)}

/* news */
.news{top:2613px;width:280px}
.news .date{position:absolute;left:0;top:0;width:60px;height:78px;background:var(--yellow);color:var(--purple);text-align:center;font-family:"Raleway",sans-serif;font-weight:700}
.news .date .m{display:block;font-size:14px;padding-top:10px}
.news .date .d{display:block;font-size:30px;line-height:34px}
.news h4{margin-left:89px;font-family:"Raleway",sans-serif;font-weight:700;font-size:16px;line-height:26px;color:var(--purple)}
.news p{margin-top:22px;font-size:11px;line-height:18px;color:var(--muted)}

/* footer */
.footer{top:2845px;left:0;width:1200px;height:346px;background:var(--footer-bg);border-top:4px solid var(--purple)}
.f-col{top:2915px}
.f-col h5{font-family:"Raleway",sans-serif;font-weight:700;font-size:12px;color:var(--purple);text-transform:uppercase;margin-bottom:14px;letter-spacing:.5px}
.f-col li{list-style:none;font-size:11px;line-height:21px;color:var(--muted)}
.f-col p{font-size:11px;line-height:19px;color:var(--muted);width:300px}
.signup{top:3005px;left:728px;display:flex}
.signup .field{width:234px;height:34px;background:var(--white);border:1px solid #ddd;font-size:11px;font-style:italic;padding:9px 10px;color:var(--ink)}
.signup .send{width:76px;height:34px;background:var(--purple);color:var(--white);font-family:"Raleway",sans-serif;font-weight:700;font-size:11px;display:flex;align-items:center;justify-content:center;text-transform:uppercase}
.f-rule{top:3107px;left:162px;width:876px;border-top:1px solid #dedede}
.copyright{top:3132px;left:162px;font-size:11px;color:var(--ink)}
.social{top:3124px;left:912px;display:flex;gap:5px}
.social span{width:27px;height:27px;border-radius:50%;background:var(--purple-mid)}
</style>
</head>
<body>

<header>
  <div class="abs topbar"></div>
  <div class="abs phone">
    <svg width="17" height="17" viewBox="0 0 24 24" aria-hidden="true"><path fill="#6b449b" d="M6.6 10.8c1.4 2.8 3.8 5.1 6.6 6.6l2.2-2.2c.3-.3.7-.4 1-.2 1.1.4 2.3.6 3.6.6.6 0 1 .4 1 1V20c0 .6-.4 1-1 1C10.6 21 3 13.4 3 4c0-.6.4-1 1-1h3.5c.6 0 1 .4 1 1 0 1.3.2 2.5.6 3.6.1.3 0 .7-.2 1z"/></svg>
    CALL US: 555.014.2290
  </div>
  <nav class="abs nav">
    <ul class="nav-list">
      <li>Home</li><li>Academics</li><li>About Us</li><li>News &amp; Events</li><li>Research</li><li class="active">Scholarships</li>
    </ul>
  </nav>
  <div class="abs brand">Amara<br>Lindell<br>Foundation</div>
</header>

<section>
  <div class="abs hero" role="img" aria-label="Photo of a smiling high school student holding books beside school lockers"></div>
  <h1 class="abs hero-title">We provide academic scholarships to high school students for college.</h1>
  <div class="abs btn-apply">Apply Now</div>
  <svg class="abs arrow" style="left:58px;top:372px" width="18" height="34" viewBox="0 0 18 34" aria-hidden="true"><path d="M16 2 2 17l14 15" fill="none" stroke="#fff" stroke-width="2"/></svg>
  <svg class="abs arrow" style="left:1124px;top:372px" width="18" height="34" viewBox="0 0 18 34" aria-hidden="true"><path d="M2 2l14 15L2 32" fill="none" stroke="#fff" stroke-width="2"/></svg>
</section>

<section class="abs audience">
  <div class="aud-col">
    <h3><span class="script">For</span> High Schools</h3>
    <p>Lorem ipsum dolor sit amet, consectetur adipiscing elit sed do eiusmod tempor incididunt ut labore et dolore magna aliqua enim ad minim magna aliquam ad min im veniam incididunt ut labore.</p>
    <span class="btn-line">Read More</span>
  </div>
  <div class="aud-col">
    <h3><span class="script">For</span> Sponsors</h3>
    <p>Lorem ipsum dolor sit amet, consectetur adipiscing elit sed do eiusmod tempor incididunt ut labore et dolore magna aliqua enim ad minim magna aliquam ad min im veniam incididunt ut labore.</p>
    <span class="btn-line">Read More</span>
  </div>
  <div class="aud-col">
    <h3><span class="script">For</span> Scholars</h3>
    <p>Lorem ipsum dolor sit amet, consectetur adipiscing elit sed do eiusmod tempor incididunt ut labore et dolore magna aliqua enim ad minim magna aliquam ad min im veniam incididunt ut labore.</p>
    <span class="btn-line">Read More</span>
  </div>
</section>

<h2 class="abs section-title" style="top:1017px;padding-top:16px"><span class="script">Featured</span>Scholarships</h2>

<article class="abs card" style="left:162px">
  <div class="photo" role="img" aria-label="Photo of a classroom full of young students" style="background:linear-gradient(135deg,#c98c6e,#d9b08f 50%,#8f6a5c)"></div>
  <h4>Finibus Bonorum etalorum</h4>
  <p>Duis aute irure dolor in reprehenderit in voluptate velit esse cillum dolore eu fugiat nulla pariatur sint occaecat cupidatat non proident, sunt in culpa qui officia deserunt mollit anim id est laborum.</p>
  <span class="btn-line">Read More</span>
</article>
<article class="abs card" style="left:464px">
  <div class="photo" role="img" aria-label="Photo of a student holding folders outdoors" style="background:linear-gradient(135deg,#b9c2b4,#8aa0b8 50%,#6b8a5e)"></div>
  <h4>Finibus Bonorum etalorum</h4>
  <p>Duis aute irure dolor in reprehenderit in voluptate velit esse cillum dolore eu fugiat nulla pariatur sint occaecat cupidatat non proident, sunt in culpa qui officia deserunt mollit anim id est laborum.</p>
  <span class="btn-line">Read More</span>
</article>
<article class="abs card" style="left:766px">
  <div class="photo" role="img" aria-label="Photo of two students reading together" style="background:linear-gradient(135deg,#d8d2cc,#a89a9c 50%,#6c5f7a)"></div>
  <h4>Finibus Bonorum etalorum</h4>
  <p>Duis aute irure dolor in reprehenderit in voluptate velit esse cillum dolore eu fugiat nulla pariatur sint occaecat cupidatat non proident, sunt in culpa qui officia deserunt mollit anim id est laborum.</p>
  <span class="btn-line">Read More</span>
</article>

<section>
  <div class="abs about"></div>
  <div class="abs about-photo" role="img" aria-label="Portrait of the young woman the foundation honors, seated in a red armchair"></div>
  <h2 class="abs about-title"><span class="script">Amara Lindell</span> FOUNDATION</h2>
  <p class="abs about-text">We are excited to announce the Amara Lindell Foundation in honor of a fabulous angel. We hope to impact the lives of individuals in the same way her dynamic spirit impacted ours. Amara, we love you and miss you everyday, and through this foundation your name will live on. Duis aute irure dolor in reprehenderit in voluptate velit esse cillum dolore eu fugiat nulla pariatur sint occaecat cupidatat non proident, sunt in culpa officia deserunt mollit anim id est laborum.</p>
</section>

<section>
  <div class="abs testimonials"></div>
  <h2 class="abs test-title script">Testimonials</h2>
  <blockquote class="abs quote"><span class="quote-mark">&ldquo;</span>Sed ut perspiciatis unde omnis iste natusiluptatem accusantium doloremque laudantium, totam rem aperiam, eaque ipsa quae ab illo inventore veritatloremis etu asi architecto beatae vitae dicta sunt explicabemo enotam remtam rem aperiamea eipsa quae ab illo inventoreim.</blockquote>
  <div class="abs quote-by">Lena &amp; Marc, City Name</div>
  <div class="abs dots"><span></span><span></span><span></span><span></span></div>
</section>

<h2 class="abs section-title" style="top:2494px;padding:14px 0 12px;border-bottom:1px solid #e3e3e3"><span class="script">News &amp;</span> Events</h2>

<article class="abs news" style="left:162px">
  <div class="date"><span class="m">FEB</span><span class="d">17</span></div>
  <h4>Finibus Bonorum ed perspiciatis undeomn ste natusere.</h4>
  <p>Duis aute irure dolor in reprehenderit in voluptate velit esse cillum dolore eu fugiat nulla pariatur sint occaecat cupidatat non proident, sunt in culpa officia deserunt mollit anim id est laborum.</p>
</article>
<article class="abs news" style="left:472px">
  <div class="date"><span class="m">FEB</span><span class="d">17</span></div>
  <h4>Finibus Bonorum ed perspiciatis undeomn ste natusere.</h4>
  <p>Duis aute irure dolor in reprehenderit in voluptate velit esse cillum dolore eu fugiat nulla pariatur sint occaecat cupidatat non proident, sunt in culpa officia deserunt mollit anim id est laborum.</p>
</article>
<article class="abs news" style="left:785px">
  <div class="date"><span class="m">FEB</span><span class="d">17</span></div>
  <h4>Finibus Bonorum ed perspiciatis undeomn ste natusere.</h4>
  <p>Duis aute irure dolor in reprehenderit in voluptate velit esse cillum dolore eu fugiat nulla pariatur sint occaecat cupidatat non proident, sunt in culpa officia deserunt mollit anim id est laborum.</p>
</article>

<footer>
  <div class="abs footer"></div>
  <div class="abs f-col" style="left:162px"><h5>Links</h5><ul><li>Sed ut satis</li><li>Onde omnis iste</li><li>Wuusit voluptat</li><li>Accusantiu</li><li>Gdolorque</li></ul></div>
  <div class="abs f-col" style="left:306px"><h5>Community</h5><ul><li>Home</li><li>About me</li><li>FAQs</li><li>Products</li><li>Contact me</li></ul></div>
  <div class="abs f-col" style="left:451px"><h5>What We Do</h5><ul><li>Sed ut perspiciatis</li><li>Onde omnis iste n</li><li>Wtus error sit volupt</li><li>Em accusantiu</li><li>Gdoloremque</li></ul></div>
  <div class="abs f-col" style="left:615px"><h5>More</h5><ul><li>Terms</li><li>Privacy</li><li>Help</li><li>Accessibility</li><li>Press</li></ul></div>
  <div class="abs f-col" style="left:728px"><h5>Email Sign Up</h5><p>Sed ut perspiciatis unde ols isteats errr sit volu ptatem accusantiusauda ntium.</p></div>
  <div class="abs signup"><div class="field">Email Address:</div><div class="send">Send Me</div></div>
  <div class="abs f-rule"></div>
  <div class="abs copyright">&copy; 2017 Amara Lindell Foundation. All Copyrights are Reserved. &nbsp;Terms of Use &nbsp; Privacy Policy &nbsp; Sitemap</div>
  <div class="abs social" aria-label="Social links"><span></span><span></span><span></span><span></span></div>
</footer>

</body>
</html>
```